Business cards to launch an education platform

Hi,
I am looking at having new business cards designed.
I am a startup, developing a web platform for schools and university, the education world. It's an online assessment system.
I would like a card that looks classy, and that is using the colors and the font of my logo.

I have attached:
1) my logo
2) A business card that I have designed quickly so you can have all the information required in the card, but I really don't like it.
3) The font that I am using (Lato Regular) to design my web platform
4) Some screenshots of my web platform so you can have a look at the style that I have.

Target Market(s)

Major market: Education system: Schools and university
Minor markets: Business in general

Industry/Entity Type

Business

Contact Information for Business Card

Clara Fenwick
Director

M: 0437 518 902
E: clara.fenwick@amberLoomSystems.com.au

Requirements
Must have
• The colors of my logo

```html
<!DOCTYPE html>
<html lang="en">
<head>
<meta charset="utf-8">
<title>Amber Loom Systems – Business Cards</title>
<link rel="stylesheet" href="https://fonts.googleapis.com/css2?family=Lato:wght@300;400&family=Roboto+Condensed:wght@400&display=swap">
<style>
  :root {
    --backdrop: #8f8f8f;
    --card-white: #eeeff1;
    --ink-navy: #163e6b;
    --ink-grey: #4a4d52;
    --brand-blue: #1c5a98;
    --brand-light: #2aa6d9;
    --back-dark: #0b3f7a;
    --back-mid: #0f5895;
    --back-light: #0d86a9;
    --back-text: #e9eef4;
  }
  * { box-sizing: border-box; margin: 0; padding: 0; }
  html, body {
    width: 1105px;
    height: 1200px;
    overflow: hidden;
    background: var(--backdrop);
  }
  .sheet {
    position: relative;
    width: 1105px;
    height: 1200px;
  }
  .card {
    position: absolute;
    left: 182px;
    width: 746px;
    height: 425px;
  }

  /* Front */
  .card-front {
    top: 120px;
    background: var(--card-white);
  }
  .brand-block {
    position: absolute;
    right: 48px;
    top: 38px;
    display: flex;
    flex-direction: column;
    align-items: flex-end;
    gap: 22px;
  }
  .brand-square {
    width: 68px;
    height: 68px;
    background: var(--brand-blue);
    margin-right: 58px;
  }
  .brand-name {
    font-family: "Lato", sans-serif;
    font-weight: 400;
    font-size: 29px;
    letter-spacing: 1px;
    color: var(--brand-blue);
  }
  .holder-name {
    position: absolute;
    left: 43px;
    top: 210px;
    font-family: "Roboto Condensed", sans-serif;
    font-size: 37px;
    color: var(--ink-navy);
  }
  .holder-role {
    position: absolute;
    left: 43px;
    top: 253px;
    font-family: "Roboto Condensed", sans-serif;
    font-size: 25px;
    color: var(--ink-grey);
  }
  .rule {
    position: absolute;
    left: 138px;
    top: 275px;
    width: 562px;
    height: 3px;
    display: flex;
    gap: 3px;
  }
  .rule span { flex: 1; height: 100%; }
  .rule span:nth-child(1) { background: var(--ink-navy); }
  .rule span:nth-child(2) { background: var(--brand-blue); }
  .rule span:nth-child(3) { background: var(--brand-light); }
  .contact-list {
    position: absolute;
    left: 46px;
    top: 303px;
    list-style: none;
    font-family: "Lato", sans-serif;
    font-size: 19px;
    color: var(--ink-grey);
  }
  .contact-list li {
    display: flex;
    align-items: center;
    gap: 12px;
    height: 29px;
  }
  .contact-icon {
    width: 18px;
    height: 18px;
    flex: none;
  }

  /* Back */
  .card-back {
    top: 638px;
    overflow: hidden;
  }
  .back-field {
    position: absolute;
    inset: 0;
    background:
      radial-gradient(ellipse at 85% 95%, var(--back-light) 0%, rgba(13,134,169,0) 55%),
      linear-gradient(135deg, var(--back-dark) 0%, var(--back-mid) 60%, #0c6f9f 100%);
  }
  .back-wordmark {
    position: absolute;
    left: 0;
    right: 0;
    top: 160px;
    text-align: center;
    font-family: "Lato", sans-serif;
    font-weight: 300;
    font-size: 50px;
    letter-spacing: 3px;
    color: var(--back-text);
  }
  .back-url {
    position: absolute;
    left: 0;
    right: 0;
    top: 260px;
    text-align: center;
    font-family: "Lato", sans-serif;
    font-weight: 400;
    font-size: 21px;
    letter-spacing: 1.5px;
    color: var(--back-text);
  }
</style>
</head>
<body>
<main class="sheet">

  <section class="card card-front" aria-label="Business card front">
    <div class="brand-block">
      <div class="brand-square"></div>
      <div class="brand-name">Amber Loom Systems</div>
    </div>

    <h1 class="holder-name">Clara Fenwick</h1>
    <p class="holder-role">Director</p>
    <div class="rule"><span></span><span></span><span></span></div>

    <ul class="contact-list">
      <li>
        <svg class="contact-icon" viewBox="0 0 18 18" aria-hidden="true">
          <rect x="4.5" y="1" width="9" height="16" rx="1.5" fill="var(--ink-navy)"/>
          <rect x="6" y="3" width="6" height="10" fill="var(--card-white)"/>
        </svg>
        0437 518 902
      </li>
      <li>
        <svg class="contact-icon" viewBox="0 0 18 18" aria-hidden="true">
          <rect x="2" y="4.5" width="14" height="9" fill="var(--ink-navy)"/>
          <path d="M2 4.5 L9 10 L16 4.5" fill="none" stroke="var(--card-white)" stroke-width="1.2"/>
        </svg>
        clara.fenwick@amberLoomSystems.com.au
      </li>
      <li>
        <svg class="contact-icon" viewBox="0 0 18 18" aria-hidden="true">
          <circle cx="9" cy="9" r="7" fill="var(--ink-navy)"/>
          <path d="M4 7 C6 6 7 9 9 8 C10 11 7 12 7 15 M11 3 C12 6 14 6 15 7" fill="none" stroke="var(--card-white)" stroke-width="1.2"/>
        </svg>
        www.amberLoomSystems.com.au
      </li>
    </ul>
  </section>

  <section class="card card-back" aria-label="Business card back">
    <div class="back-field" role="img" aria-label="Deep blue background with a large faint brand emblem decoration"></div>
    <p class="back-wordmark">Amber Loom Systems</p>
    <p class="back-url">amberLoomSystems.com.au</p>
  </section>

</main>
</body>
</html>
```